printing company neeeds a trifold design

I need a trifold brochure (8.5 x 11) flat size, then folded to a trifold that will highlight about a dozen of my most popular products. Should be modern, with just enough of a sales tool. I attached a few thing that I have but looking for something special. I can supply images or you can use place holders?
Updates

The brochure with the "eye" on the front panel is my most current trifold and you can follow that for most of the content. I might edit that later on

Please DO NOT copy my design. Looking for something fresh, new and interesting. I added my old one to show some content and images.
Thanks all!!!!

good morning I am looking for something different. Fresh, modern, clean (neeeds to be cohesive and able to be branded for social media, postcards etc.) and No "eye" or just a small one. . You can use some of the pics and some of the content. This needs to be sales piece I sent out to prospective clients.
Show that we are professional, personal and do great work. 3rd generation printer that is responsive and reaches out to all that respond. All types of Printing, Large format like signs and banners, Realesate, small biz, trade show products look at kornbluthpress.com

Designs look the same

Target Market(s)

Small business, real eststate firms, local business, professionals

Industry/Entity Type

I am in the printing and sign business... 2 of my websites are kornbluthpress.com and kornbluthtypeworks.com

Requirements
Must have
• a front panel with contact info and company logo that I can send over, a panel about my company and images
Nice to have
• something stylish, easy to read with impact. Needs to be something people will wanty to knao more abouit and top reach out
Should not have
• The same look as what I sent over.

```html
<!DOCTYPE html>
<html lang="en">
<head>
<meta charset="utf-8">
<title>Kornbluth Press — Trifold Brochure</title>
<link href="https://fonts.googleapis.com/css2?family=Oswald:wght@400;500&family=Roboto+Condensed:wght@300;400&family=Montserrat:wght@400&display=swap" rel="stylesheet">
<style>
  :root{
    --magenta:#ff1fd2;
    --cyan:#3fd0f5;
    --ink:#111111;
    --panel-grey:#f1f3f2;
    --white:#ffffff;
    --yellow:#ffe626;
    --kraft:#b98a5c;
  }
  *{box-sizing:border-box;margin:0;padding:0}
  html,body{width:1200px;height:927px;overflow:hidden;background:var(--white)}
  .brochure{position:relative;width:1200px;height:927px;display:flex;font-family:"Roboto Condensed",sans-serif;color:var(--ink)}

  /* Left panel */
  .panel-showcase{width:397px;height:927px;background:var(--magenta);position:relative}
  .product-card{position:absolute;left:33px;width:330px;height:236px;background:var(--white)}
  .product-card .product-photo{position:absolute;left:23px;top:18px;width:287px;height:158px}
  .product-card h3{position:absolute;left:0;right:0;top:182px;text-align:center;font-family:"Oswald",sans-serif;font-weight:400;font-size:27px;color:var(--magenta);letter-spacing:.2px}
  .card-1{top:49px}
  .card-2{top:303px}
  .card-3{top:557px}
  .photo-cards{background:linear-gradient(135deg,#d9b43a 0%,#2a2a2a 35%,#3ab3d6 70%,#1e3f7a 100%)}
  .photo-postcards{background:linear-gradient(160deg,#e8b45a 0%,#8fd3c9 45%,#7c7de6 100%)}
  .photo-catalogs{background:linear-gradient(120deg,#2b4f8a 0%,#3a3a3a 40%,#d9483f 60%,#1d3d63 100%)}
  .site-url{position:absolute;left:0;right:0;top:840px;text-align:center;color:var(--white);font-family:"Roboto Condensed",sans-serif;font-weight:300;font-size:26px}

  /* Middle panel */
  .panel-services{width:398px;height:927px;background:var(--panel-grey);position:relative}
  .panel-services h2{position:absolute;left:37px;top:40px;font-family:"Oswald",sans-serif;font-weight:500;font-size:39px;color:var(--cyan);letter-spacing:.5px}
  .service-list{position:absolute;left:47px;top:122px;list-style:none}
  .service-list li{height:36.4px;display:flex;align-items:center;font-size:16.5px;font-weight:300}
  .service-list svg{width:9px;height:12px;margin-right:15px;margin-top:-10px;flex:none}
  .services-photo{position:absolute;left:24px;top:751px;width:349px;height:176px;background:linear-gradient(90deg,#2a2a2a 0%,#2a2a2a 34%,#f3efe6 36%,#e9d8b8 64%,#c8283a 67%,#3a2f6e 100%)}

  /* Right panel */
  .panel-about{width:405px;height:927px;background:var(--white);position:relative}
  .about-copy{position:absolute;left:34px;top:42px;width:323px}
  .about-copy h2{font-family:"Oswald",sans-serif;font-weight:500;font-size:38px;line-height:46px;margin-bottom:8px}
  .about-copy p{font-size:15px;font-weight:300;line-height:22.7px;text-align:justify;margin-bottom:22px}
  .about-copy h3{font-family:"Oswald",sans-serif;font-weight:500;font-size:29px;line-height:34.5px;margin-top:-6px;margin-bottom:4px;text-transform:uppercase}
  .help-list{list-style:none;margin-bottom:16px}
  .help-list li{position:relative;padding-left:12px;font-size:15px;font-weight:300;line-height:22.7px}
  .help-list li::before{content:"";position:absolute;left:0;top:10px;width:5px;height:5px;background:var(--ink)}
  .signoff{font-family:"Oswald",sans-serif;font-weight:500;font-size:21px;margin-top:12px;line-height:26px}
  .signature{font-family:"Montserrat",sans-serif;font-size:20px;line-height:30px}
  .ink-band{position:absolute;left:5px;bottom:0;width:400px;height:136px}
</style>
</head>
<body>
<main class="brochure">
  <section class="panel-showcase">
    <article class="product-card card-1">
      <div class="product-photo photo-cards" role="img" aria-label="Photo of assorted printed business cards"></div>
      <h3>BUSINESS CARDS</h3>
    </article>
    <article class="product-card card-2">
      <div class="product-photo photo-postcards" role="img" aria-label="Photo of printed postcards for a childcare academy"></div>
      <h3>POSTCARDS</h3>
    </article>
    <article class="product-card card-3">
      <div class="product-photo photo-catalogs" role="img" aria-label="Photo of printed catalogs and brochures"></div>
      <h3>CATALOGS</h3>
    </article>
    <p class="site-url">www.kornbluthpress.com</p>
  </section>

  <section class="panel-services">
    <h2>OUR SERVICES</h2>
    <ul class="service-list">
      <li><svg viewBox="0 0 9 12"><path d="M1 0 L8 7 L4.5 7 L6 11 L4.5 11.5 L3 7.5 L1 10 Z" fill="var(--cyan)"/></svg>Business Cards</li>
      <li><svg viewBox="0 0 9 12"><path d="M1 0 L8 7 L4.5 7 L6 11 L4.5 11.5 L3 7.5 L1 10 Z" fill="var(--cyan)"/></svg>Brochures &amp; Menus</li>
      <li><svg viewBox="0 0 9 12"><path d="M1 0 L8 7 L4.5 7 L6 11 L4.5 11.5 L3 7.5 L1 10 Z" fill="var(--cyan)"/></svg>Postcards</li>
      <li><svg viewBox="0 0 9 12"><path d="M1 0 L8 7 L4.5 7 L6 11 L4.5 11.5 L3 7.5 L1 10 Z" fill="var(--cyan)"/></svg>Presentation Folders</li>
      <li><svg viewBox="0 0 9 12"><path d="M1 0 L8 7 L4.5 7 L6 11 L4.5 11.5 L3 7.5 L1 10 Z" fill="var(--cyan)"/></svg>Booklets &amp; Catalogs</li>
      <li><svg viewBox="0 0 9 12"><path d="M1 0 L8 7 L4.5 7 L6 11 L4.5 11.5 L3 7.5 L1 10 Z" fill="var(--cyan)"/></svg>Raffle Tickets</li>
      <li><svg viewBox="0 0 9 12"><path d="M1 0 L8 7 L4.5 7 L6 11 L4.5 11.5 L3 7.5 L1 10 Z" fill="var(--cyan)"/></svg>Letterpress Printing</li>
      <li><svg viewBox="0 0 9 12"><path d="M1 0 L8 7 L4.5 7 L6 11 L4.5 11.5 L3 7.5 L1 10 Z" fill="var(--cyan)"/></svg>Wedding Invitations</li>
      <li><svg viewBox="0 0 9 12"><path d="M1 0 L8 7 L4.5 7 L6 11 L4.5 11.5 L3 7.5 L1 10 Z" fill="var(--cyan)"/></svg>Save the Date Items</li>
      <li><svg viewBox="0 0 9 12"><path d="M1 0 L8 7 L4.5 7 L6 11 L4.5 11.5 L3 7.5 L1 10 Z" fill="var(--cyan)"/></svg>Business Announcements</li>
      <li><svg viewBox="0 0 9 12"><path d="M1 0 L8 7 L4.5 7 L6 11 L4.5 11.5 L3 7.5 L1 10 Z" fill="var(--cyan)"/></svg>Greeting Cards</li>
      <li><svg viewBox="0 0 9 12"><path d="M1 0 L8 7 L4.5 7 L6 11 L4.5 11.5 L3 7.5 L1 10 Z" fill="var(--cyan)"/></svg>Signs &amp; Banners</li>
      <li><svg viewBox="0 0 9 12"><path d="M1 0 L8 7 L4.5 7 L6 11 L4.5 11.5 L3 7.5 L1 10 Z" fill="var(--cyan)"/></svg>Retractable Banners</li>
      <li><svg viewBox="0 0 9 12"><path d="M1 0 L8 7 L4.5 7 L6 11 L4.5 11.5 L3 7.5 L1 10 Z" fill="var(--cyan)"/></svg>A-Frame Signs &amp; Flags</li>
      <li><svg viewBox="0 0 9 12"><path d="M1 0 L8 7 L4.5 7 L6 11 L4.5 11.5 L3 7.5 L1 10 Z" fill="var(--cyan)"/></svg>Event Tents</li>
      <li><svg viewBox="0 0 9 12"><path d="M1 0 L8 7 L4.5 7 L6 11 L4.5 11.5 L3 7.5 L1 10 Z" fill="var(--cyan)"/></svg>Posters</li>
      <li><svg viewBox="0 0 9 12"><path d="M1 0 L8 7 L4.5 7 L6 11 L4.5 11.5 L3 7.5 L1 10 Z" fill="var(--cyan)"/></svg>Canvas Prints and more</li>
    </ul>
    <div class="services-photo" role="img" aria-label="Photo of printed menus and flyers laid on kraft paper"></div>
  </section>

  <section class="panel-about">
    <div class="about-copy">
      <h2>ABOUT US</h2>
      <p>We are Kornbluth Press, your expert printing source for everything from business cards to brochures, large format printing, signs &amp; banners We have you covered.</p>
      <p>For 3 generations, Kornbluth Press has been serving professionals, businesses and organizations like yours, helping them grow their brand and prosper</p>
      <h3>Kornbluth Press can help you and your business grow!</h3>
      <ul class="help-list">
        <li>Event and Trade Show Materials</li>
        <li>Every Door Direct Mail Campaigns</li>
        <li>Real Estate Signs &amp; Marketing Materials</li>
        <li>Large Format Printing: Posters, Signs and Banners<br>of all types</li>
      </ul>
      <h3>We are looking forward to working with you and for you!</h3>
      <p class="signoff">Thank You,</p>
      <p class="signature">Dana Kornbluth</p>
    </div>
    <svg class="ink-band" viewBox="0 0 400 136" role="img" aria-label="Decorative CMYK ink splash band">
      <defs>
        <linearGradient id="fade" x1="0" y1="0" x2="0" y2="1">
          <stop offset="0" stop-color="#fff" stop-opacity="1"/>
          <stop offset=".45" stop-color="#fff" stop-opacity="0"/>
        </linearGradient>
      </defs>
      <rect x="0" y="40" width="87" height="96" fill="var(--cyan)"/>
      <rect x="87" y="30" width="119" height="106" fill="var(--magenta)"/>
      <rect x="206" y="45" width="77" height="91" fill="var(--yellow)"/>
      <rect x="283" y="20" width="117" height="116" fill="var(--ink)"/>
      <rect x="0" y="0" width="400" height="136" fill="url(#fade)"/>
    </svg>
  </section>
</main>
</body>
</html>
```